Advanced Therapeutic Massage Therapist

I need a business card advertising my massage services as an advanced therapeutic massage therapist. I offer advanced therapeutic massage, swedish and deep tissue. I want to create a simple, professional and feminine card. I like bright colours and creativity.

I prefer a bold and experimental approach rather than something status-quo. A card to suggest therapeutic healing through dynamic massage. Motifs, shapes or layout which suggest movement and flow.
Updates

Target Market(s)

Everybody!

Industry/Entity Type

Health And Wellness

Contact Information for Business Card

The card should include:
My name, logo, services offered and my contact details.

Sláine Dunleavy
Massage Therapist

- Swedish - Deep Tissue - Advanced Therapeutic

Phone: (+353) 87 216 4093
Email: regenerate@slainedunleavy-example.com
Website: www.slainedunlevy-example.com

Font styles to use
Serif
Sans Serif
Decorative
Script

Colors

Designer to choose colors to be used in the design.

Requirements
Must have
• An example may contain something like this, yet concise:
• "Sláine Dunleavy
• Massage Therapist
• - Swedish - Deep Tissue - Advanced Therapeutic"
Nice to have
• This sentence is optional:
• Imagery such as a logo or symbol. I have attached a file containing a logo I had produced however the name is incorrect now as it is "Sláine" not "Nelly". It could be edited to change it to Sláine.
• I have sent the file as .psd .jpg. .pdf and .png
• I like when the card conveys energy, movement, pressure points, flow etc.
• I just like the designer to follow their own style and ideas. I like bright colours but must have a lot of a base colour to offset it. I really prefer them to follow their own inspiration. That is my preference.
Should not have
• Pine trees, non-native trees to Britain and Ireland, exotic flowers or animals that are not native to Britain and Ireland.
• I don't like brown as the background colour of the card.
• The cars shouldn't look like a wedding invitation i.e too many floral type designs.

```html
<!DOCTYPE html>
<html lang="en">
<head>
<meta charset="utf-8">
<title>Sláine Dunleavy – Massage Therapist Business Card</title>
<link rel="stylesheet" href="https://fonts.googleapis.com/css2?family=Great+Vibes&family=Questrial&display=swap">
<style>
  :root {
    --stage: #6a6a6a;
    --mint-light: #d5efe6;
    --mint: #a9e2d3;
    --mint-deep: #8fd6c4;
    --ink: #2f3a38;
    --charcoal: #232323;
    --white: #f4f4f4;
    --sea-green: #6fbf9f;
    --gold-light: #e8c77a;
    --gold: #c49a3e;
    --gold-deep: #9c7426;
  }
  * { margin: 0; padding: 0; box-sizing: border-box; }
  html, body {
    width: 1200px;
    height: 550px;
    overflow: hidden;
    background: var(--stage);
  }
  .stage {
    position: relative;
    width: 1200px;
    height: 550px;
    border: 1px solid #888;
  }
  .card {
    position: absolute;
    top: 157px;
    width: 390px;
    height: 236px;
    text-align: center;
    overflow: hidden;
  }
  .card--front {
    left: 195px;
    background:
      radial-gradient(ellipse 60% 45% at 30% 25%, var(--mint-light) 0%, transparent 70%),
      radial-gradient(ellipse 50% 40% at 75% 70%, var(--mint-deep) 0%, transparent 70%),
      radial-gradient(ellipse 45% 35% at 20% 85%, var(--mint-deep) 0%, transparent 70%),
      var(--mint);
  }
  .card--back {
    left: 614px;
    background: var(--charcoal);
    border-top: 1px solid #bbb;
  }
  .logo-mark {
    position: absolute;
    left: 145px;
    top: 44px;
    width: 100px;
    height: 100px;
  }
  .name {
    position: absolute;
    left: 0;
    width: 100%;
    font-family: "Great Vibes", cursive;
    font-weight: 400;
    font-size: 24px;
    line-height: 26px;
    white-space: nowrap;
  }
  .role {
    position: absolute;
    left: 0;
    width: 100%;
    font-family: "Questrial", sans-serif;
    font-size: 9.5px;
    letter-spacing: 0.08em;
    line-height: 11px;
    white-space: nowrap;
  }
  .card--front .name { top: 157px; color: var(--ink); }
  .card--front .role { top: 184px; color: var(--ink); padding-left: 8px; }
  .card--back .name { top: 66px; color: var(--white); }
  .card--back .role { top: 92px; color: var(--white); padding-left: 10px; }
  .contact {
    position: absolute;
    top: 117px;
    left: 0;
    width: 100%;
    list-style: none;
    font-family: "Questrial", sans-serif;
    font-size: 11px;
    line-height: 17px;
    color: var(--white);
    white-space: nowrap;
  }
  .services {
    position: absolute;
    top: 210px;
    left: 0;
    width: 100%;
    font-family: "Questrial", sans-serif;
    font-size: 10.5px;
    line-height: 13px;
    color: var(--sea-green);
    white-space: nowrap;
  }
</style>
</head>
<body>
<main class="stage">
  <section class="card card--front">
    <svg class="logo-mark" viewBox="0 0 100 100" role="img" aria-label="Logo mark area: round gold emblem">
      <defs>
        <radialGradient id="gold-fill" cx="40%" cy="35%" r="70%">
          <stop offset="0%" stop-color="#e8c77a"/>
          <stop offset="60%" stop-color="#c49a3e"/>
          <stop offset="100%" stop-color="#9c7426"/>
        </radialGradient>
      </defs>
      <circle cx="50" cy="50" r="49" fill="url(#gold-fill)"/>
    </svg>
    <h1 class="name">Sláine Dunleavy</h1>
    <p class="role">massage therapist</p>
  </section>

  <section class="card card--back">
    <h2 class="name">Sláine Dunleavy</h2>
    <p class="role">massage therapist</p>
    <ul class="contact">
      <li>(+353) 87 216 4093</li>
      <li>slaine@slainedunleavy-example.com</li>
      <li>www.slainedunlevy-example.com</li>
    </ul>
    <p class="services">Swedish - Deep Tissue - Advanced Therapeutic</p>
  </section>
</main>
</body>
</html>
```